Website for International Non-Profit for Birth Parent Searching

LumaKin is a 501(c)(3) non-profit organization that helps Chinese adoptees search and reunite with birth families who were separated due the One Child Policy in China. We want to create a website that can link to an information database that allows website users to easily access information around search ads in an organized way; help connect families to professional searchers; provide resources for community support for adoptees and their families as they embark on a personal and emotional journey of finding birth family through support groups on social media and consultation/education on the searching process; and provide the opportunity for the adoptive community to give back through donations and volunteer opportunities. The final design should foster a sense of community and be easy navigable to access the multiple resources we provide to help families search for each other. We would like to see designs with red/black/white color schemes that are gentle, inviting, and family friendly to viewers. We would like to see some design layouts with Chinese themes, if possible.

```html
<!DOCTYPE html>
<html lang="en">
<head>
<meta charset="utf-8">
<title>LumaKin</title>
<link href="https://fonts.googleapis.com/css2?family=Lato:wght@400;700;900&display=swap" rel="stylesheet">
<style>
:root{
  --red:#e50914;
  --black:#0b0b0b;
  --ink:#222;
  --text:#3d3d3d;
  --grey:#e6e6e6;
  --white:#fff;
}
*{box-sizing:border-box;margin:0;padding:0}
html,body{width:1200px;height:3416px;overflow:hidden}
body{font-family:'Lato',sans-serif;color:var(--text);background:var(--white);position:relative}
a{color:inherit;text-decoration:none}
.btn{display:inline-block;background:var(--red);color:#fff;font-weight:700;font-size:16px;text-transform:uppercase;text-align:center}
.btn-outline{display:inline-block;border:2px solid var(--red);color:#fff;font-weight:700;font-size:16px;text-transform:uppercase;width:180px;height:58px;line-height:54px;text-align:center}

/* top bar */
.topbar{position:absolute;top:0;left:0;width:1200px;height:54px;background:var(--black);color:#fff;font-size:14px}
.topbar .info{position:absolute;left:74px;top:0;height:54px;display:flex;align-items:center;gap:28px}
.topbar .info span{display:flex;align-items:center;gap:12px}
.topbar .search{position:absolute;right:0;top:0;width:345px;height:54px;background:var(--grey);clip-path:polygon(0 0,100% 0,100% 100%,28px 100%);color:#222;font-weight:700;font-size:14px;display:flex;align-items:center;padding-left:70px;gap:22px}

/* nav */
.nav{position:absolute;top:54px;left:0;width:1200px;height:83px;background:#fff;display:flex;align-items:center}
.logo{position:absolute;left:74px;font-size:30px;font-weight:700;color:var(--ink)}
.menu{position:absolute;left:274px;display:flex;gap:30px;font-size:14px;font-weight:700;color:#333}
.menu .active{color:var(--red)}
.donate{position:absolute;right:74px;top:23px;width:120px;height:38px;line-height:38px;font-size:14px}

/* hero */
.hero{position:absolute;top:137px;left:0;width:1200px;height:537px;background:linear-gradient(120deg,#6d7a4e 0%,#c9b29c 35%,#e6d8cc 55%,#a48a76 80%,#5d4b3c 100%);text-align:center;color:#fff}
.hero h1{position:absolute;top:155px;width:100%;font-size:58px;font-weight:900;text-shadow:0 2px 6px rgba(0,0,0,.35)}
.hero p{position:absolute;top:225px;left:250px;width:700px;font-size:28px;font-weight:700;line-height:37px;text-shadow:0 2px 6px rgba(0,0,0,.35)}
.hero .btn{position:absolute;top:315px;left:510px;width:180px;height:58px;line-height:58px}
.dots{position:absolute;top:488px;left:564px;display:flex;gap:8px}
.dots i{width:12px;height:12px;border-radius:50%;background:#fff;display:block}
.dots i.on{background:transparent;border:2px solid #fff;width:14px;height:14px;margin-top:-1px}

/* welcome */
.welcome{position:absolute;top:674px;left:0;width:1200px;height:488px}
.welcome h2{position:absolute;left:74px;top:84px;font-size:34px;font-weight:700;color:var(--ink)}
.welcome p{position:absolute;left:74px;top:140px;width:500px;font-size:15px;line-height:27px}
.welcome .btn{position:absolute;left:74px;top:333px;width:180px;height:58px;line-height:58px}
.welcome .photo{position:absolute;left:613px;top:59px;width:587px;height:364px;background:linear-gradient(135deg,#f2f3f5 0%,#d9dee2 45%,#8fa0b5 70%,#eef0f2 100%);clip-path:polygon(0 0,100% 0,100% 100%,58px 100%)}

/* services */
.services{position:absolute;top:1162px;left:0;width:1200px;height:659px;background:var(--black);color:#fff;text-align:center}
.services h2{position:absolute;top:60px;width:100%;font-size:34px;font-weight:700}
.services .lead{position:absolute;top:116px;width:100%;font-size:15px}
.cards{position:absolute;top:178px;left:74px;display:flex;gap:29px}
.card{width:331px}
.card .img{height:199px}
.card h3{margin-top:22px;font-size:24px;font-weight:400}
.card p{margin-top:8px;font-size:15px;line-height:25px;padding:0 4px;height:75px}
.card .btn-outline{margin-top:26px}

/* how */
.how{position:absolute;top:1821px;left:0;width:1200px;height:477px;text-align:center}
.how h2{position:absolute;top:50px;width:100%;font-size:34px;font-weight:700;color:var(--ink)}
.steps{position:absolute;top:150px;left:74px;display:flex;gap:29px}
.step{width:331px}
.step svg{display:block;margin:0 auto}
.step h3{margin-top:18px;color:var(--red);font-size:24px;font-weight:700}
.step p{margin-top:10px;font-size:15px;line-height:27px}

/* testimonials */
.testi{position:absolute;top:2298px;left:0;width:1200px;height:385px}
.testi .photo{position:absolute;left:0;top:0;width:600px;height:385px;background:linear-gradient(120deg,#efe9e2 0%,#c9a48a 45%,#b22e2e 70%,#e8ddd2 100%)}
.testi .panel{position:absolute;left:495px;top:0;width:705px;height:385px;background:var(--red);clip-path:polygon(105px 0,100% 0,100% 100%,0 100%);color:#fff}
.testi h2{position:absolute;left:120px;top:62px;font-size:34px;font-weight:700}
.testi blockquote{position:absolute;left:120px;top:112px;width:530px;font-size:14px;font-style:italic;line-height:27px}
.testi .name{position:absolute;left:121px;top:236px;font-size:14px;font-weight:700}
.testi .pager{position:absolute;left:121px;top:294px;display:flex;gap:11px}
.testi .pager i{width:12px;height:12px;border-radius:50%;background:#fff;display:block}
.testi .pager i.on{background:#111}

/* contact */
.contact{position:absolute;top:2683px;left:0;width:1200px;height:418px}
.contact .info{position:absolute;left:0;top:0;width:497px;height:418px;background:var(--black);color:#fff}
.contact h2{position:absolute;left:74px;top:45px;font-size:34px;font-weight:700}
.contact h3{position:absolute;left:74px;top:105px;font-size:23px;font-weight:700}
.contact ul{position:absolute;left:78px;top:145px;list-style:none;font-size:15px;line-height:25px}
.contact ul li{display:flex;align-items:center;gap:20px}
.contact h4{position:absolute;left:76px;top:245px;font-size:18px;font-weight:700}
.hours{position:absolute;left:78px;top:287px;font-size:15px;line-height:25px;border-collapse:collapse}
.hours td{padding:0}
.hours td:first-child{width:130px}
.contact .map{position:absolute;left:497px;top:0;width:703px;height:418px;background:linear-gradient(135deg,#e9eef0 0%,#dfe6e3 40%,#a9c8dc 60%,#f1ead6 100%)}

/* footer */
.footer{position:absolute;top:3101px;left:0;width:1200px;height:251px}
.footer h3{color:var(--red);font-size:23px;font-weight:700}
.col{position:absolute;top:57px}
.col p{margin-top:12px;font-size:14px;line-height:22px}
.about{left:74px;width:340px}
.sitemap{left:489px}
.sitemap .links{margin-top:12px;display:grid;grid-template-columns:100px 100px;row-gap:9px;font-size:14px}
.email{left:793px;width:335px}
.email form{margin-top:24px;display:flex;height:44px}
.email .field{flex:1;background:#ececec;font-size:13px;color:#555;padding-left:16px;line-height:44px}
.email .go{width:63px;background:var(--red);color:#fff;font-weight:700;font-size:16px;line-height:44px;text-align:center}

.bottom{position:absolute;top:3352px;left:0;width:1200px;height:64px;background:var(--black);color:#ddd;font-size:12px}
.bottom .copy{position:absolute;left:74px;top:27px}
.bottom .social{position:absolute;right:72px;top:24px;display:flex;gap:20px}
.bottom .social i{width:16px;height:16px;border-radius:50%;background:#aaa;display:block}
</style>
</head>
<body>

<header class="topbar">
  <div class="info">
    <span><svg width="10" height="14" viewBox="0 0 10 14"><path d="M5 0a5 5 0 0 0-5 5c0 4 5 9 5 9s5-5 5-9a5 5 0 0 0-5-5zm0 7a2 2 0 1 1 0-4 2 2 0 0 1 0 4z" fill="#fff"/></svg>412 Willow Lane, Brookfield, BF2 7QL</span>
    <span><svg width="13" height="13" viewBox="0 0 24 24"><path d="M6.6 10.8a15 15 0 0 0 6.6 6.6l2.2-2.2c.3-.3.7-.4 1-.2 1.1.4 2.3.6 3.6.6.6 0 1 .4 1 1V20c0 .6-.4 1-1 1A17 17 0 0 1 3 4c0-.6.4-1 1-1h3.5c.6 0 1 .4 1 1 0 1.3.2 2.5.6 3.6.1.3 0 .7-.2 1z" fill="#fff"/></svg>1-800-555-0142</span>
    <span><svg width="14" height="11" viewBox="0 0 14 11"><path d="M0 0h14v11H0z" fill="#fff"/><path d="M0 0l7 6 7-6" fill="none" stroke="#0b0b0b" stroke-width="1.4"/></svg>hello@lumakin.org</span>
  </div>
  <div class="search">
    <svg width="14" height="14" viewBox="0 0 14 14"><circle cx="5.5" cy="5.5" r="4.3" fill="none" stroke="#222" stroke-width="2"/><path d="M9 9l4 4" stroke="#222" stroke-width="2.2"/></svg>
    SEARCH ADS
  </div>
</header>

<nav class="nav">
  <a class="logo" href="#">LumaKin</a>
  <div class="menu">
    <a class="active" href="#">HOME</a><a href="#">ABOUT US</a><a href="#">SERVICES</a><a href="#">BLOG</a><a href="#">NEWS &amp; EVENTS</a><a href="#">TESTIMONIALS</a><a href="#">CONTACT US</a>
  </div>
  <a class="btn donate" href="#">DONATE</a>
</nav>

<section class="hero" role="img" aria-label="Photo of a smiling family playing together outdoors">
  <h1>LUMAKIN</h1>
  <p>Helping Chinese adoptees and birth families find their way back to each other.</p>
  <a class="btn" href="#">START SEARCH</a>
  <div class="dots"><i class="on"></i><i></i><i></i><i></i></div>
</section>

<section class="welcome">
  <h2>Welcome to LumaKin</h2>
  <p>LumaKin is a 501(c)(3) non-profit helping Chinese adoptees search for and reunite with birth families separated under the One Child Policy. We gather search ads into one organized database, connect families with trusted professional searchers, and offer support groups and education so no one walks this personal and emotional journey alone.</p>
  <a class="btn" href="#">OUR MISSION</a>
  <div class="photo" role="img" aria-label="Photo of parents lifting a happy toddler in a bright room"></div>
</section>

<section class="services">
  <h2>Our Services</h2>
  <p class="lead">Search, connect and give back: resources for every step of the journey to find family again.</p>
  <div class="cards">
    <div class="card">
      <div class="img" role="img" aria-label="Photo of an older couple browsing search ads on a laptop" style="background:linear-gradient(135deg,#d8d0c4,#a88b70 60%,#6e5a48)"></div>
      <h3>Search Ads Database</h3>
      <p>Browse birth family and adoptee search ads, sorted by province, city, finding date and orphanage.</p>
      <a class="btn-outline" href="#">BROWSE ADS</a>
    </div>
    <div class="card">
      <div class="img" role="img" aria-label="Photo of a family meeting with a professional searcher" style="background:linear-gradient(135deg,#eef0f4,#b7c3d6 55%,#3a3f4a)"></div>
      <h3>Professional Searchers</h3>
      <p>We connect families with vetted searchers in China and offer consultation on the search process.</p>
      <a class="btn-outline" href="#">FIND A SEARCHER</a>
    </div>
    <div class="card">
      <div class="img" role="img" aria-label="Photo of young parents with their baby" style="background:linear-gradient(135deg,#f3f3f1,#c9c2b8 55%,#5b4d44)"></div>
      <h3>Donate &amp; Volunteer</h3>
      <p>Give back to the adoptive community through donations or by volunteering your time and skills.</p>
      <a class="btn-outline" href="#">GET INVOLVED</a>
    </div>
  </div>
</section>

<section class="how">
  <h2>How It Works</h2>
  <div class="steps">
    <div class="step">
      <svg width="66" height="66" viewBox="0 0 66 66" fill="none" stroke="#222" stroke-width="2"><rect x="4" y="4" width="52" height="58" rx="3"/><rect x="9" y="9" width="42" height="48"/><rect x="14" y="16" width="6" height="5"/><path d="M24 18h20"/><rect x="14" y="27" width="6" height="5"/><path d="M24 29h20"/><rect x="14" y="38" width="6" height="5"/><path d="M24 40h12"/><path d="M40 56l18-18 5 5-18 18-7 2z"/></svg>
      <h3>Free Register</h3>
      <p>Create a free account to save searches, receive match alerts and join our private support groups for adoptees and their families.</p>
    </div>
    <div class="step">
      <svg width="66" height="66" viewBox="0 0 66 66" fill="none" stroke="#222" stroke-width="2.4"><path d="M10 4h32l14 14v44H10z"/><path d="M42 4v14h14"/><path d="M20 30h26M20 38h26M20 46h26"/></svg>
      <h3>Post a Search Ad</h3>
      <p>Share finding details, dates and photos in one organized ad that birth families and searchers across China can easily find.</p>
    </div>
    <div class="step">
      <svg width="70" height="66" viewBox="0 0 70 66" fill="none" stroke="#222" stroke-width="2.2"><circle cx="35" cy="18" r="10"/><circle cx="14" cy="22" r="8"/><circle cx="56" cy="22" r="8"/><path d="M18 62V48c0-9 8-16 17-16s17 7 17 16v14z"/><path d="M14 44c-7 0-12 5-12 11v7h16"/><path d="M56 44c7 0 12 5 12 11v7H52"/></svg>
      <h3>Reunite Family</h3>
      <p>When a possible match appears, we guide DNA testing and first contact, with caring support before and after reunion.</p>
    </div>
  </div>
</section>

<section class="testi">
  <div class="photo" role="img" aria-label="Photo of a family in winter clothes holding red envelopes"></div>
  <div class="panel">
    <h2>Family Stories</h2>
    <blockquote>“ After years of searching on our own, LumaKin helped us organize our search ad and connected us with a searcher in Hunan. Their support group carried us through every step, and last spring our daughter met her birth parents for the very first time.”</blockquote>
    <div class="name">-ADOPTIVE PARENT</div>
    <div class="pager"><i class="on"></i><i></i><i></i><i></i></div>
  </div>
</section>

<section class="contact">
  <div class="info">
    <h2>Contact Info</h2>
    <h3>LUMAKIN</h3>
    <ul>
      <li><svg width="10" height="14" viewBox="0 0 10 14"><path d="M5 0a5 5 0 0 0-5 5c0 4 5 9 5 9s5-5 5-9a5 5 0 0 0-5-5zm0 7a2 2 0 1 1 0-4 2 2 0 0 1 0 4z" fill="#fff"/></svg>412 Willow Lane, Brookfield, BF2 7QL</li>
      <li><svg width="12" height="12" viewBox="0 0 24 24"><path d="M6.6 10.8a15 15 0 0 0 6.6 6.6l2.2-2.2c.3-.3.7-.4 1-.2 1.1.4 2.3.6 3.6.6.6 0 1 .4 1 1V20c0 .6-.4 1-1 1A17 17 0 0 1 3 4c0-.6.4-1 1-1h3.5c.6 0 1 .4 1 1 0 1.3.2 2.5.6 3.6.1.3 0 .7-.2 1z" fill="#fff"/></svg>1-800-555-0142</li>
      <li><svg width="13" height="10" viewBox="0 0 14 11"><path d="M0 0h14v11H0z" fill="#fff"/><path d="M0 0l7 6 7-6" fill="none" stroke="#0b0b0b" stroke-width="1.4"/></svg>hello@lumakin.org</li>
    </ul>
    <h4>Hour:</h4>
    <table class="hours">
      <tr><td>Monday - Friday</td><td>10am - 6pm</td></tr>
      <tr><td>Saturday</td><td>&nbsp;10 am - 5pm</td></tr>
      <tr><td>Sunday</td><td>&nbsp;Closed</td></tr>
    </table>
  </div>
  <div class="map" role="img" aria-label="Street map showing the office location"></div>
</section>

<footer class="footer">
  <div class="col about">
    <h3>About LumaKin</h3>
    <p>A 501(c)(3) non-profit helping Chinese adoptees and birth families separated by the One Child Policy search for and find each other, with community support, education and trusted searchers at every step.</p>
  </div>
  <div class="col sitemap">
    <h3>Site Map</h3>
    <div class="links"><a href="#">Home</a><a href="#">Search Ads</a><a href="#">About Us</a><a href="#">Donate</a><a href="#">Services</a><a href="#">Volunteer</a><a href="#">Blog</a><a href="#">Contact Us</a></div>
  </div>
  <div class="col email">
    <h3>Newsletter</h3>
    <p>Get new search ads, reunion stories and volunteer news in your inbox</p>
    <form><div class="field">Enter Email Address</div><div class="go">GO</div></form>
  </div>
</footer>

<div class="bottom">
  <div class="copy">Copyright © 2021. LumaKin All Right Reserved</div>
  <div class="social"><i></i><i></i><i></i><i></i><i></i></div>
</div>

</body>
</html>
```